Hi,
We are also sourcing for a logo, if you have ideas please take a look at our other project (if you look at our profile you should be able to see it).
We are looking for a website that will be used to manage mobile devices. The feature set is rather small, users can Wipe, Lock, Locate devices as well as make them Ring or Speak (by sending text to be spoken). We attached some images of what it looks like right now. We are looking for simplicity, uniformity and most importantly, the website should be thought of as primary User Interface, it should flow.
Please see attached to get an idea of what it looks like now. The current design was inspired by making a site that will work and flow well on a variety of displays (from mobile to tablet to desktop).
We want to stay away from radio buttons, check-boxes. This should be engaging and creative, opposite of Corporate. Not busy (ideally we are looking to have fewest possible choices at any given time and at the same time no feature should be more than 3 clicks away (this is a suggestion/approximation... just want to share our understanding of what 'flow' is).
Could be cartoony.
Thanks!
BrisketLoom
Reason: there are a couple of designs that are interesting, in addition to specific feedback I provided, possibly looking for more concepts.
Thank You

```html
<!DOCTYPE html>
<html lang="en">
<head>
<meta charset="utf-8">
<title>BrisketLoom — Device Manager</title>
<link rel="stylesheet" href="https://fonts.googleapis.com/css2?family=Ropa+Sans&display=swap">
<style>
  :root {
    --brand-dark: #2c4a3b;
    --brand-mid: #3f6652;
    --brand-light: #5f8a73;
    --nav-text: #e8efe9;
    --page-bg: #ffffff;
    --text: #3d3d3d;
    --title: #555555;
    --border: #dcdcdc;
    --btn-light-top: #ffffff;
    --btn-light-bottom: #e4e4e4;
    --map-a: #ece6d2;
    --map-b: #dde6c6;
  }
  * { box-sizing: border-box; margin: 0; padding: 0; }
  html, body {
    width: 1200px; height: 1200px; overflow: hidden;
    background: var(--page-bg);
    font-family: "Ropa Sans", "Arial Narrow", sans-serif;
    color: var(--text);
  }
  .site-header {
    position: absolute; left: 0; top: 0; width: 1200px; height: 62px;
    background: var(--brand-dark);
    border-bottom: 2px solid #c9d3cd;
  }
  .brand {
    position: absolute; left: 88px; top: 15px;
    display: flex; align-items: center; gap: 14px;
    color: var(--nav-text); font-size: 25px;
  }
  .brand-mark { width: 30px; height: 30px; border-radius: 50%; background: var(--brand-light); }
  .main-nav { position: absolute; right: 86px; top: 19px; display: flex; gap: 40px; }
  .main-nav a { color: var(--nav-text); text-decoration: none; font-size: 19px; }
  .main-nav .caret { font-size: 11px; margin-left: 4px; vertical-align: middle; }

  .actions {
    position: absolute; top: 83px; left: 346px;
    display: flex; gap: 21px;
  }
  .action {
    width: 69px; height: 56px;
    display: flex; align-items: center; justify-content: center;
    border: 1px solid #d4d4d4;
    background: linear-gradient(var(--btn-light-top), var(--btn-light-bottom));
    box-shadow: 0 2px 3px rgba(0,0,0,0.15);
    font-size: 20px; color: #333;
  }
  .action.is-active {
    background: linear-gradient(var(--brand-light), var(--brand-dark));
    color: #fff; border-color: var(--brand-dark);
  }
  .action.is-loading { font-size: 12px; }

  .device-map {
    position: absolute; left: 165px; top: 157px; width: 873px; height: 540px;
    background: linear-gradient(160deg, var(--map-a), var(--map-b));
  }

  .card {
    position: absolute; top: 737px; height: 391px;
    border: 1px solid var(--border);
    box-shadow: 0 1px 3px rgba(0,0,0,0.08);
    padding: 22px 24px 0 25px;
  }
  .card-welcome { left: 87px; width: 306px; }
  .card-lost { left: 435px; width: 310px; padding-left: 30px; }
  .card-secure { left: 787px; width: 330px; padding-left: 31px; padding-right: 41px; }
  .card-title { font-weight: normal; font-size: 26px; color: var(--title); height: 49px; }
  .card-photo { height: 140px; margin-bottom: 14px; }
  .photo-phones { width: 182px; background: linear-gradient(#3a3a3a, #9a9a9a); }
  .photo-pocket { width: 218px; background: linear-gradient(135deg, #e8e8e8, #5f7490); }
  .photo-bear { width: 168px; margin-left: 5px; background: linear-gradient(135deg, #f2f2f2, #b5b5b8); }
  .card-text { font-size: 15px; line-height: 18px; text-align: justify; }
  .read-more {
    position: absolute; right: 23px; bottom: 16px;
    padding: 5px 9px; border-radius: 8px;
    background: linear-gradient(var(--brand-light), var(--brand-dark));
    color: #fff; font-size: 15px; text-decoration: none;
    box-shadow: 0 0 0 2px #e4e4e4;
  }

  .site-footer {
    position: absolute; top: 1155px; left: 89px; width: 1027px;
    display: flex; justify-content: space-between; font-size: 15px; color: #444;
  }
  .footer-links { padding-top: 3px; }
  .footer-links a { color: #444; text-decoration: none; }
  .footer-links .sep { margin: 0 4px; }
</style>
</head>
<body>
  <header class="site-header">
    <div class="brand"><span class="brand-mark"></span><span>BrisketLoom</span></div>
    <nav class="main-nav">
      <a href="#">admin<span class="caret">▼</span></a>
      <a href="#">devices</a>
      <a href="#">settings</a>
      <a href="#">sign out</a>
    </nav>
  </header>

  <div class="actions">
    <div class="action is-active">Wipe</div>
    <div class="action">lock</div>
    <div class="action">find</div>
    <div class="action">ring</div>
    <div class="action">speak</div>
    <div class="action is-loading">Loading</div>
  </div>

  <div class="device-map" role="img" aria-label="Street map showing the device location"></div>

  <section class="card card-welcome">
    <h2 class="card-title">Welcome</h2>
    <div class="card-photo photo-phones" role="img" aria-label="Three smartphones side by side"></div>
    <p class="card-text">Lorem Ipsum is simply dummy text of the printing and typesetting industry. Lorem Ipsum has been the industry's standard dummy text ever since the 1500s, when an unknown printer took a galley of type and scrambled it to make a type specimen book.</p>
    <a class="read-more" href="#">Read More</a>
  </section>

  <section class="card card-lost">
    <h2 class="card-title">Lost or Stolen Phone?</h2>
    <div class="card-photo photo-pocket" role="img" aria-label="Hand taking a phone from a jeans pocket"></div>
    <p class="card-text">Lorem Ipsum is simply dummy text of the printing and typesetting industry. Lorem Ipsum has been the industry's standard dummy text ever since the 1500s, when an unknown printer took a galley of type and scrambled it to make a type specimen book.</p>
    <a class="read-more" href="#">Read More</a>
  </section>

  <section class="card card-secure">
    <h2 class="card-title">Protect &amp; Secure</h2>
    <div class="card-photo photo-bear" role="img" aria-label="Toy bear with a phone beside a laptop"></div>
    <p class="card-text">Lorem Ipsum is simply dummy text of the printing and typesetting industry. Lorem Ipsum has been the industry's standard dummy text ever since the 1500s, when an unknown printer took a galley of type and scrambled it to make a type specimen book.</p>
    <a class="read-more" href="#">Read More</a>
  </section>

  <footer class="site-footer">
    <div>Copyrights © 2012. All Rights Reserved.</div>
    <div class="footer-links">
      <a href="#">Terms and Conditions</a><span class="sep">|</span>
      <a href="#">Frequently Asked Questions</a><span class="sep">|</span>
      <a href="#">About</a><span class="sep">|</span>
      <a href="#">Contact</a>
    </div>
  </footer>
</body>
</html>
```